Flyer, poster, banner and social media titles designs for Community Mending Chartre

The Harbourline Charter for Community Mending provide a nationally agreed framework to guide recovery policy and practice across Australia. The Principles support recovery practitioners, governments, non-government organisations and communities to deliver effective, community-centred recovery outcomes.
The Principles have recently been refreshed through extensive consultation and we require a contemporary visual identity and design suite that will increase awareness, engagement and practical application of the Principles.
The redesign will cover:
• A4 Brochure (primary publication)
• A3 Poster
• Pull up banner
• Social Media Tiles
The new design should:
• Create a recognisable brand for the Harbourline Charter.
• Appeal to both experienced and emerging recovery practitioners.
• Reflect contemporary disaster recovery practice.
• Feel people-focused rather than government-focused.
• Support future resources such as videos, implementation guides, presentations and workshop materials.
• Remain relevant for several years without requiring a major redesign.
Target Audience
• Disaster recovery practitioners
• Government agencies
• Non-government organisations
• Community recovery workers
• Recovery managers and leaders
• Community stakeholders and volunteers
The visual identity should reflect the six Principles:
• Understanding Context
• Recognising Complexity
• Community-Centred Approaches
• Coordination
• Communication
• Capacity Building
The design should communicate:
• Recovery is centred on people and communities.
• Recovery is collaborative and involves many sectors.
• Recovery is adaptive, inclusive and evidence-informed.
• Recovery supports resilience and long-term wellbeing.
• The Principles provide practical guidance for recovery practice.
We are looking for:
• Modern and professional
• Warm and approachable
• Human-centred
• Inclusive and accessible
• Australian in context
• Visually engaging
• Suitable for print and digital use
We would like to avoid:
• Images of disaster destruction
• Emergency response imagery (fire trucks, flashing lights, etc.)
• Overly corporate or bureaucratic designs
• Designs that focus on deficits rather than recovery and growth
Consider themes such as:
• Connection and collaboration
• Communities and people
• Growth, recovery and renewal
Accessibility
Designs should:
• Meet accessibility best practice
• Use clear typography
• Achieve strong colour contrast
• Be suitable for both digital and print formats

Deliverables
1. Principles Brochure
• A4 trifold size x 2 (online and print friendly version)
• A side to include cover side, logos side and overview of principles.
• B side full details of the principles
• Graphic to highlight the 3 c’s concept (RECOVERY Context, complexity, community centred, coordinate, communicate and capacity). Currently 3 circles.
• Can be printed and distributed electronically
2. Poster
• A1 and A3 versions
• Suitable for office and workshop display
3. Pull-Up Banner - 850 mm (W) × 2000 mm (H)
• Conference and event use
• High visual impact
• Strong branding and concise messaging
4. Social Media Tiles x 3

We are providing an extension and increasing the budget following feedback from designers. We are wanting the resources to look and feel different from the existing designs, considering either a different colour palette in the designs or different motif with the leave design. Any nature based designs should consider the Australian fauna or flora. Also suggest avoiding images in the designs. The principles are not numbered or liner in the concept of how they function. Happy to answer any further questions and thank you for your suggested concepts.

Disaster recovery practitioners, Government agencies , Non-government organisations, Community recovery workers and Community stakeholders and volunteers

Disaster recovery

• Modern, warm, visually engaging, human-centred, Australian in context and different to the current design.
• Symbols for each principles
• Images of disaster destruction, Emergency response imagery, Overly corporate or bureaucratic designs, Designs that focus on deficits rather than recovery and growth, avoid too much black

```html
<!DOCTYPE html>
<html lang="en">
<head>
<meta charset="utf-8">
<title>Harbourline Charter for Community Mending – Design Suite</title>
<link href="https://fonts.googleapis.com/css2?family=Outfit:wght@400;500;600&family=Source+Sans+3:wght@400;600;700&display=swap" rel="stylesheet">
<style>
:root{
  --sheet:#f1eee7;
  --cream:#f7f0e2;
  --ink:#1d3640;
  --deep:#133c48;
  --olive:#7b8a2f;
  --olive-light:#a9bb4c;
  --teal:#3e8c8b;
  --gold:#c89a2c;
  --orange:#c8692b;
  --blue:#2e6b8c;
  --purple:#6a5a86;
  --body:#2f3d42;
}
*{box-sizing:border-box;margin:0;padding:0}
html,body{width:1200px;height:800px;overflow:hidden;background:var(--sheet)}
body{position:relative;font-family:"Source Sans 3",Arial,sans-serif;color:var(--body)}
.abs{position:absolute}

.piece-label{position:absolute;font-family:"Outfit",Arial,sans-serif;font-size:12.5px;font-weight:600;color:#1b2a30;text-align:center;line-height:1.3;letter-spacing:.2px}
.piece-label small{display:block;font-size:11px;font-weight:400}

.eyebrow{font-family:"Outfit",Arial,sans-serif;text-transform:uppercase;font-weight:500;letter-spacing:.3px}
.title-line{font-family:"Outfit",Arial,sans-serif;font-weight:500;line-height:.98;display:block}
.on-dark .title-top{color:#f4efe2}
.on-dark .title-bottom{color:var(--olive-light)}
.on-light .title-top{color:var(--deep)}
.on-light .title-bottom{color:var(--olive)}

.art{position:absolute}
.wheel-text{font-family:"Outfit",Arial,sans-serif}

/* Brochure outside */
.brochure-out{left:17px;top:54px;width:413px;height:383px;box-shadow:0 1px 3px rgba(0,0,0,.12);overflow:hidden}
.panel{position:absolute;top:0;height:100%;overflow:hidden}
.panel-cover{left:0;width:138px;background:var(--deep);padding:23px 10px 0 18px;color:#e9e4d6}
.panel-cover .eyebrow{font-size:9px;line-height:1.25;color:#f4efe2}
.panel-cover .title-line{font-size:21px}
.panel-cover p{font-size:7px;line-height:1.55;margin-top:9px}
.panel-partners{left:138px;width:129px;background:var(--cream);padding:24px 12px 0 16px}
.panel-partners h3{font-family:"Outfit",Arial,sans-serif;font-size:7px;font-weight:500;color:#1b2a30;letter-spacing:.3px;margin-bottom:15px}
.partner{display:flex;align-items:center;gap:8px;height:36px;font-size:6.3px;line-height:1.25;color:#1b2a30}
.partner .dot{width:18px;height:18px;border-radius:50%;flex:none}
.panel-partners .closing{font-size:7px;line-height:1.55;color:#1b2a30;margin-top:22px}
.panel-principles{left:267px;width:146px;background:var(--deep);padding:23px 14px 0 15px;color:#e9e4d6}
.panel-principles h3{font-family:"Outfit",Arial,sans-serif;font-size:10px;font-weight:500;color:var(--olive-light);margin-bottom:10px}
.panel-principles p{font-size:7px;line-height:1.55;margin-bottom:8px}

/* Poster */
.poster{left:442px;top:54px;width:333px;height:487px;background:var(--cream);overflow:hidden;box-shadow:0 1px 3px rgba(0,0,0,.12)}
.poster .eyebrow{position:absolute;left:21px;top:24px;font-size:12.5px;color:var(--deep)}
.poster .title{position:absolute;left:20px;top:44px}
.poster .title-line{font-size:40px}
.poster .tagline{position:absolute;left:21px;top:132px;font-size:11px;line-height:1.3;color:#1b2a30}
.values{position:absolute;left:14px;right:14px;top:384px;display:flex}
.value{flex:1;text-align:center;font-size:7.3px;line-height:1.35;color:#1b2a30;border-left:1px solid #dcd3c0;padding:0 3px}
.value:first-child{border-left:none}
.value .ico{width:22px;height:22px;border:1.6px solid var(--olive);border-radius:50%;margin:0 auto 7px}
.poster-footer{position:absolute;left:0;right:0;bottom:0;height:38px;background:var(--olive);color:#fff;text-align:center;padding-top:6px;line-height:1.35}
.poster-footer strong{display:block;font-weight:600;font-size:9px}
.poster-footer span{display:block;font-size:7.5px}

/* Banner */
.banner{left:795px;top:55px;width:165px;height:523px;background:var(--cream);overflow:hidden;box-shadow:0 1px 4px rgba(0,0,0,.18)}
.banner-head{position:absolute;left:0;top:0;width:100%;height:140px;background:var(--deep);padding:28px 10px 0 22px;clip-path:polygon(0 0,100% 0,100% 100%,0 88%)}
.banner-head .eyebrow{font-size:8.5px;color:#f4efe2}
.banner-head .title-line{font-size:25px}
.banner-statement{position:absolute;left:22px;top:148px;width:125px;font-size:9px;line-height:1.35;color:#1b2a30}
.banner-list{position:absolute;left:22px;top:200px;list-style:none}
.banner-list li{display:flex;align-items:center;gap:8px;height:30px;font-family:"Outfit",Arial,sans-serif;font-size:6.6px;font-weight:600;text-transform:uppercase;line-height:1.2;width:125px}
.banner-list .dot{width:20px;height:20px;border-radius:50%;flex:none;border:2px solid rgba(255,255,255,.55)}
.banner-foot{position:absolute;left:0;bottom:0;width:100%;height:155px;background:var(--deep);padding:44px 10px 0 22px;color:#f4efe2;clip-path:polygon(0 14%,100% 0,100% 100%,0 100%)}
.banner-foot p{font-size:8.5px;line-height:2.05}
.banner-foot .url{font-size:8.5px;color:var(--olive-light);margin-top:18px}

/* Social tiles */
.tile{left:986px;width:188px;overflow:hidden;box-shadow:0 1px 3px rgba(0,0,0,.12)}
.tile-centre{top:59px;height:178px;background:var(--cream)}
.tile-adapt{top:248px;height:182px;background:var(--deep)}
.tile-future{top:440px;height:148px;background:var(--cream)}
.tile .quote{position:absolute;font-family:"Outfit",Arial,sans-serif;font-size:13px;line-height:1.38}
.tile .mark{position:absolute;left:16px;white-space:nowrap}
.tile .mark .eyebrow{font-size:5.3px;display:block}
.tile .mark .brand{font-family:"Outfit",Arial,sans-serif;font-size:12.5px;line-height:1.1}

/* Brochure inside */
.brochure-in{left:17px;top:543px;width:760px;height:235px;background:var(--cream);display:flex;box-shadow:0 1px 3px rgba(0,0,0,.12)}
.principle{flex:1;border-left:1px solid #e4dbc9;padding-top:14px}
.principle:first-child{border-left:none}
.principle-head{height:31px;display:flex;align-items:center;gap:6px;padding:0 6px;color:#fff;font-family:"Outfit",Arial,sans-serif;font-weight:600;font-size:7.2px;text-transform:uppercase;line-height:1.15}
.principle-head .ico{width:17px;height:17px;border:1.4px solid rgba(255,255,255,.85);border-radius:50%;flex:none}
.principle-body{padding:10px 9px 0 11px;font-size:6.4px;line-height:1.5;color:#1b2a30}
.principle-body ul{list-style:none;margin-top:8px}
.principle-body li{position:relative;padding-left:7px;margin-bottom:5px}
.principle-body li::before{content:"";position:absolute;left:0;top:3px;width:2.5px;height:2.5px;border-radius:50%;background:#1b2a30}

/* Three Cs */
.three-cs{left:805px;top:609px;width:376px;height:171px;background:var(--cream);box-shadow:0 1px 3px rgba(0,0,0,.12)}
.three-cs h3{position:absolute;left:59px;top:15px;font-family:"Outfit",Arial,sans-serif;font-size:8px;font-weight:500;color:var(--deep);letter-spacing:.2px}
.three-cs .copy{position:absolute;left:243px;top:30px;width:120px;font-size:7.6px;line-height:1.42;color:#1b2a30}
.three-cs .copy strong{font-weight:700}
</style>
</head>
<body>

<svg width="0" height="0" style="position:absolute" aria-hidden="true">
  <defs>
    <symbol id="recovery-wheel" viewBox="-105 -105 210 210">
      <g stroke="#f7f0e2" stroke-width="3">
        <path fill="#7b8a2f" d="M-58.8,-80.9 A100,100 0 0 1 58.8,-80.9 L21.2,-29.1 A36,36 0 0 0 -21.2,-29.1 Z"/>
        <path fill="#3e8c8b" d="M58.8,-80.9 A100,100 0 0 1 95.1,30.9 L34.2,11.1 A36,36 0 0 0 21.2,-29.1 Z"/>
        <path fill="#c89a2c" d="M95.1,30.9 A100,100 0 0 1 0,100 L0,36 A36,36 0 0 0 34.2,11.1 Z"/>
        <path fill="#c8692b" d="M0,100 A100,100 0 0 1 -95.1,30.9 L-34.2,11.1 A36,36 0 0 0 0,36 Z"/>
        <path fill="#6a5a86" d="M-95.1,30.9 A100,100 0 0 1 -58.8,-80.9 L-21.2,-29.1 A36,36 0 0 0 -34.2,11.1 Z"/>
      </g>
      <circle r="35" fill="#f7f0e2"/>
      <g fill="none" stroke="#fff" stroke-width="1.4">
        <circle cx="0" cy="-80" r="7"/>
        <circle cx="63" cy="-35" r="7"/>
        <circle cx="46" cy="36" r="7"/>
        <circle cx="-44" cy="36" r="7"/>
        <circle cx="-63" cy="-35" r="7"/>
      </g>
      <g class="wheel-text" fill="#fff" font-family="Outfit, Arial, sans-serif" font-size="7" font-weight="600" text-anchor="middle">
        <text x="0" y="-62">UNDERSTANDING<tspan x="0" dy="9">CONTEXT</tspan></text>
        <text x="64" y="-16">RECOGNISING<tspan x="64" dy="9">COMPLEXITY</tspan></text>
        <text x="46" y="55">COMMUNITY-<tspan x="46" dy="9">CENTRED</tspan><tspan x="46" dy="9">APPROACHES</tspan></text>
        <text x="-44" y="58" font-size="6.6">COORDINATION</text>
        <text x="-63" y="-16">CAPACITY<tspan x="-63" dy="9">BUILDING</tspan></text>
      </g>
      <circle cx="0" cy="-12" r="6" fill="none" stroke="#7b8a2f" stroke-width="1.4"/>
      <text x="0" y="8" text-anchor="middle" font-family="Outfit, Arial, sans-serif" font-size="11" font-weight="600" fill="#133c48">RECOVERY</text>
    </symbol>
  </defs>
</svg>

<!-- Piece labels -->
<div class="piece-label" style="left:107px;top:15px;width:200px">A4 TRIFOLD BROCHURE<small>OUTSIDE</small></div>
<div class="piece-label" style="left:508px;top:15px;width:200px">A3 POSTER</div>
<div class="piece-label" style="left:780px;top:15px;width:200px">PULL-UP BANNER<small>850 x 2000mm</small></div>
<div class="piece-label" style="left:980px;top:15px;width:200px">SOCIAL MEDIA TILES<small>1080 x 1080px</small></div>
<div class="piece-label" style="left:57px;top:504px;width:240px">A4 TRIFOLD BROCHURE<small>INSIDE (DETAILS OF PRINCIPLES)</small></div>

<!-- Brochure outside -->
<section class="abs brochure-out">
  <div class="panel panel-cover on-dark">
    <div class="eyebrow">Harbourline<br>Charter for</div>
    <div style="margin-top:4px">
      <span class="title-line title-top">Community</span>
      <span class="title-line title-bottom">Mending</span>
    </div>
    <p>Disasters can deeply impact lives and livelihoods. Working with communities to recover is complex, challenging and long-term.</p>
    <p>These principles guide our efforts, our approach, our planning and our decision-making to support effective, community-centred recovery.</p>
    <div class="art" role="img" aria-label="Native foliage illustration" style="left:0;bottom:0;width:138px;height:120px;background:radial-gradient(ellipse at 35% 70%,rgba(169,187,76,.55),rgba(62,140,139,.25) 55%,rgba(19,60,72,0) 75%)"></div>
  </div>
  <div class="panel panel-partners">
    <h3>PARTNERS IN RECOVERY</h3>
    <div class="partner"><span class="dot" style="background:#1b2a30"></span>Federal Partners Office</div>
    <div class="partner"><span class="dot" style="background:var(--blue)"></span>State and Territory<br>Governments</div>
    <div class="partner"><span class="dot" style="background:var(--teal)"></span>Local Councils<br>Alliance</div>
    <div class="partner"><span class="dot" style="background:var(--orange)"></span><b>Harbourline<br>Relief Aid</b></div>
    <div class="partner"><span class="dot" style="background:var(--blue)"></span>Non-Government<br>Organisations</div>
    <div class="partner"><span class="dot" style="background:var(--olive)"></span>Community<br>Organisations</div>
    <p class="closing">Working together for stronger, more resilient communities.</p>
  </div>
  <div class="panel panel-principles">
    <h3>THE PRINCIPLES</h3>
    <p>A nationally agreed framework to guide recovery policy and practice across Australia.</p>
    <p>The principles are interconnected and work together to support effective, inclusive and sustainable recovery.</p>
  </div>
  <svg class="abs" style="left:258px;top:220px" width="152" height="152" role="img" aria-label="Recovery principles wheel"><use href="#recovery-wheel"/></svg>
</section>

<!-- A3 Poster -->
<section class="abs poster on-light">
  <div class="art" role="img" aria-label="Native foliage illustration" style="left:200px;top:10px;width:150px;height:220px;background:radial-gradient(ellipse at 60% 45%,rgba(62,140,139,.75),rgba(123,138,47,.45) 45%,rgba(247,240,226,0) 72%)"></div>
  <div class="eyebrow">Harbourline Charter for</div>
  <div class="title">
    <span class="title-line title-top">Community</span>
    <span class="title-line title-bottom">Mending</span>
  </div>
  <p class="tagline">Guiding recovery together.<br>Building stronger,<br>more resilient<br>communities.</p>
  <svg class="abs" style="left:66px;top:174px" width="206" height="206" role="img" aria-label="Recovery principles wheel"><use href="#recovery-wheel"/></svg>
  <div class="values">
    <div class="value"><div class="ico"></div>People and communities at the centre</div>
    <div class="value"><div class="ico"></div>Working together across sectors</div>
    <div class="value"><div class="ico"></div>Adaptive, inclusive and evidence-informed</div>
    <div class="value"><div class="ico"></div>Supporting resilience and long-term wellbeing</div>
  </div>
  <div class="poster-footer"><strong>Stronger together. Recovering today. Building tomorrow.</strong><span>Learn more at communitymending.org.au</span></div>
</section>

<!-- Pull-up banner -->
<section class="abs banner">
  <div class="banner-head on-dark">
    <div class="eyebrow">Harbourline Charter for</div>
    <div style="margin-top:5px">
      <span class="title-line title-top">Community</span>
      <span class="title-line title-bottom">Mending</span>
    </div>
  </div>
  <p class="banner-statement">A shared framework for effective, inclusive and sustainable recovery.</p>
  <ul class="banner-list">
    <li style="color:var(--olive)"><span class="dot" style="background:var(--olive)"></span>Understanding context</li>
    <li style="color:var(--teal)"><span class="dot" style="background:var(--teal)"></span>Recognising complexity</li>
    <li style="color:#a77d1e"><span class="dot" style="background:var(--gold)"></span>Community-centred approaches</li>
    <li style="color:var(--orange)"><span class="dot" style="background:var(--orange)"></span>Coordination</li>
    <li style="color:var(--blue)"><span class="dot" style="background:var(--blue)"></span>Communication</li>
    <li style="color:var(--purple)"><span class="dot" style="background:var(--purple)"></span>Capacity building</li>
  </ul>
  <div class="banner-foot">
    <p>People at the centre.<br>Stronger together.<br>Better for tomorrow.</p>
    <p class="url">communitymending.org.au</p>
    <div class="art" role="img" aria-label="Native foliage illustration" style="right:0;bottom:20px;width:60px;height:110px;background:radial-gradient(ellipse at 70% 50%,rgba(200,154,44,.55),rgba(19,60,72,0) 70%)"></div>
  </div>
</section>

<!-- Social tiles -->
<section class="abs tile tile-centre">
  <div class="art" role="img" aria-label="Native foliage illustration" style="right:0;top:0;width:72px;height:178px;background:linear-gradient(160deg,rgba(123,138,47,.7),rgba(62,140,139,.8) 60%,rgba(19,60,72,.85))"></div>
  <p class="quote" style="left:18px;top:31px;color:var(--teal)">People at<br>the centre.<br>Communities<br>lead the way.</p>
  <div class="mark" style="top:140px"><span class="eyebrow" style="color:var(--deep)">Harbourline Charter for</span><span class="brand" style="color:var(--deep)">Community <span style="color:var(--olive)">Mending</span></span></div>
</section>
<section class="abs tile tile-adapt">
  <div class="art" role="img" aria-label="Native foliage illustration" style="right:0;bottom:0;width:70px;height:110px;background:radial-gradient(ellipse at 75% 65%,rgba(169,187,76,.55),rgba(19,60,72,0) 70%)"></div>
  <p class="quote" style="left:18px;top:26px;color:#f4efe2">Together<br>we adapt,<br>collaborate<br>and recover.</p>
  <div class="mark" style="top:143px"><span class="eyebrow" style="color:#f4efe2">Harbourline Charter for</span><span class="brand" style="color:#f4efe2">Community <span style="color:var(--olive-light)">Mending</span></span></div>
</section>
<section class="abs tile tile-future">
  <div class="art" role="img" aria-label="Native foliage illustration" style="left:0;top:0;width:62px;height:148px;background:linear-gradient(160deg,rgba(200,105,43,.75),rgba(200,154,44,.55) 50%,rgba(123,138,47,.5))"></div>
  <p class="quote" style="left:90px;top:20px;color:var(--orange)">Building<br>resilient<br>communities<br>for the future.</p>
  <div class="mark" style="left:auto;right:10px;top:118px;text-align:right"><span class="eyebrow" style="color:var(--deep)">Harbourline Charter for</span><span class="brand" style="color:var(--deep);font-size:11.5px">Community <span style="color:var(--olive)">Mending</span></span></div>
</section>

<!-- Brochure inside -->
<section class="abs brochure-in">
  <article class="principle">
    <div class="principle-head" style="background:var(--olive)"><span class="ico"></span>Understanding<br>context</div>
    <div class="principle-body">
      <p>Successful recovery is based on understanding the community context, history, values, culture and environment.</p>
      <ul>
        <li>Acknowledge strengths and capacity</li>
        <li>Appreciate risks and stressors</li>
        <li>Be inclusive, equitable and culturally safe</li>
        <li>Support those at greater risk</li>
        <li>Respect connections to Country and environment</li>
        <li>Support long-term recovery shaped by community needs</li>
      </ul>
    </div>
  </article>
  <article class="principle">
    <div class="principle-head" style="background:var(--teal)"><span class="ico"></span>Recognising<br>complexity</div>
    <div class="principle-body">
      <p>Successful recovery responds to the complex and evolving nature of disasters and impacts.</p>
      <ul>
        <li>Impacts are complex and change over time</li>
        <li>Needs, wants and expectations evolve</li>
        <li>Flexible action is essential</li>
        <li>Different perspectives may create tensions</li>
        <li>Support helps people and communities heal and grow</li>
      </ul>
    </div>
  </article>
  <article class="principle">
    <div class="principle-head" style="background:var(--gold)"><span class="ico"></span>Community-centred<br>approaches</div>
    <div class="principle-body">
      <p>Successful recovery is led with communities, empowering them to shape their own recovery.</p>
      <ul>
        <li>Actively involve community in decisions</li>
        <li>Respect local knowledge, culture and priorities</li>
        <li>Build on local strengths and leadership</li>
        <li>Support shared responsibility</li>
        <li>Adapt to changing needs</li>
      </ul>
    </div>
  </article>
  <article class="principle">
    <div class="principle-head" style="background:var(--orange)"><span class="ico"></span>Coordination</div>
    <div class="principle-body">
      <p>Successful recovery requires coordination and partnership across all sectors.</p>
      <ul>
        <li>Plan and coordinate together</li>
        <li>Share goals and information</li>
        <li>Align roles and resources</li>
        <li>Evidence-informed decisions</li>
        <li>Transparent and accountable</li>
        <li>Build strong partnerships</li>
      </ul>
    </div>
  </article>
  <article class="principle">
    <div class="principle-head" style="background:var(--blue)"><span class="ico"></span>Communication</div>
    <div class="principle-body">
      <p>Successful recovery is built on clear, inclusive and consistent communication.</p>
      <ul>
        <li>Two-way and respectful communication</li>
        <li>Timely, accurate and accessible information</li>
        <li>Use multiple channels</li>
        <li>Listen, learn and act</li>
        <li>Keep sharing key messages</li>
      </ul>
    </div>
  </article>
  <article class="principle">
    <div class="principle-head" style="background:var(--purple)"><span class="ico"></span>Capacity building</div>
    <div class="principle-body">
      <p>Successful recovery builds on and strengthens the capacity and resilience of people, communities and organisations.</p>
      <ul>
        <li>Build individual and community skills</li>
        <li>Strengthen organisations and networks</li>
        <li>Invest in learning and development</li>
        <li>Support innovation and improvement</li>
        <li>Enable future readiness</li>
      </ul>
    </div>
  </article>
</section>

<!-- Three Cs -->
<section class="abs three-cs">
  <h3>THE THREE C'S OF RECOVERY</h3>
  <svg class="abs" style="left:40px;top:30px" width="190" height="140" viewBox="0 0 190 140" role="img" aria-label="Three overlapping circles: Context, Complexity, Community Centred">
    <g style="mix-blend-mode:multiply">
      <circle cx="66" cy="48" r="38" fill="#7b8a2f" opacity=".92"/>
      <circle cx="124" cy="48" r="38" fill="#3e8c8b" opacity=".88"/>
      <circle cx="95" cy="96" r="38" fill="#c89a2c" opacity=".9"/>
    </g>
    <circle cx="95" cy="64" r="9" fill="#133c48" opacity=".6"/>
    <g fill="#f7f0e2" font-family="Outfit, Arial, sans-serif" font-weight="600" text-anchor="middle">
      <text x="56" y="50" font-size="9">CONTEXT</text>
      <text x="136" y="50" font-size="9">COMPLEXITY</text>
      <text x="95" y="78" font-size="5.5">RECOVERY</text>
      <text x="95" y="110" font-size="8.5">COMMUNITY</text>
      <text x="95" y="122" font-size="8.5">CENTRED</text>
    </g>
  </svg>
  <p class="copy">Effective recovery happens when we <strong>Understand the Context, Recognise Complexity,</strong> and use <strong>Community-Centred Approaches.</strong><br><span style="display:block;margin-top:6px">These foundations strengthen everything we do together.</span></p>
</section>

</body>
</html>
```